TALVORE GROUP OF CLINICS

We need a medical & lab report file. The design should be healthcare related. Our current file design has been used for almost 10 years. We need something more fresh & up-to-date. We have attached the current file design.

Need extra days to review

```html
<!DOCTYPE html>
<html lang="en">
<head>
<meta charset="utf-8">
<title>Talvore Group of Clinics – Medical Report Folder</title>
<link rel="stylesheet" href="https://fonts.googleapis.com/css2?family=Chewy&family=Fredoka:wght@500;600;700&family=Open+Sans:wght@400;600;700&display=swap">
<style>
  :root{
    --stage:#d9dadc;
    --navy:#3a3b8c;
    --ink:#1d2a55;
    --blue-deep:#1c6fb6;
    --blue:#2a8fd6;
    --sky:#4cbbec;
    --white:#ffffff;
    --grey-light:#e6e7e9;
  }
  *{box-sizing:border-box;margin:0;padding:0}
  html,body{width:1200px;height:847px;overflow:hidden;background:var(--stage)}
  ul{list-style:none}
  .spread{position:absolute;left:40px;top:28px;width:1120px;height:791px;display:flex;box-shadow:0 6px 24px rgba(0,0,0,.25)}
  .page{position:relative;width:560px;height:791px;overflow:hidden}

  /* back cover */
  .back{background:linear-gradient(160deg,var(--blue) 0%,var(--blue-deep) 100%)}
  .back .anatomy-fill{position:absolute;left:60px;top:40px;width:440px;height:720px;border-radius:200px 200px 120px 120px;
    background:radial-gradient(ellipse at 50% 40%,rgba(150,200,240,.35),rgba(40,120,190,0) 70%)}
  .group-title{position:absolute;left:120px;top:62px;width:390px;height:50px;background:var(--white);border-radius:25px;
    font-family:"Fredoka",sans-serif;font-weight:700;font-size:25px;color:var(--navy);letter-spacing:.5px;
    display:flex;align-items:center;justify-content:center}
  .clinic-list{position:absolute;left:30px;top:128px;width:500px}
  .clinic{position:relative;height:92px}
  .clinic-card{position:absolute;left:36px;top:11px;width:464px;height:70px;border-radius:35px;background:var(--sky);
    border:2px dashed var(--white);padding:8px 18px 0 66px;
    font-family:"Open Sans",sans-serif;font-size:9px;line-height:12px;color:var(--ink);white-space:nowrap;overflow:hidden}
  .clinic-name{font-weight:700;color:var(--navy);font-size:10px;text-transform:uppercase}
  .clinic-mark{position:absolute;left:4px;top:8px;width:76px;height:76px;border-radius:50%;background:var(--white);
    border:2px dashed var(--sky);box-shadow:0 0 0 3px var(--white)}

  /* front cover */
  .front{background:var(--grey-light)}
  .front svg{position:absolute;left:0;top:0}
  .brand{position:absolute;left:95px;top:60px;width:180px;text-align:center;
    font-family:"Open Sans",sans-serif;font-weight:700;font-size:13px;color:var(--navy)}
  .brand-dot{width:44px;height:44px;border-radius:50%;background:var(--navy);margin:0 auto 10px}
  .report-title{position:absolute;left:345px;top:80px;width:200px;text-align:center;
    font-family:"Fredoka",sans-serif;font-weight:700;font-size:46px;line-height:44px;color:var(--navy)}
  .tagline{position:absolute;left:262px;top:200px;width:292px;height:30px;background:var(--white);
    font-family:"Chewy","Fredoka",cursive;font-size:21px;color:var(--blue);display:flex;align-items:center;justify-content:center;letter-spacing:.5px}
  .confidential{position:absolute;left:335px;top:280px;width:210px;text-align:center;
    font-family:"Open Sans",sans-serif;font-size:19px;line-height:26px;color:var(--white);letter-spacing:.5px}
</style>
</head>
<body>
<main class="spread">

  <section class="page back">
    <div class="anatomy-fill" role="img" aria-label="Faint anatomical illustration of the human torso"></div>
    <h1 class="group-title">TALVORE GROUP OF CLINICS</h1>
    <ul class="clinic-list">
      <li class="clinic"><div class="clinic-card"><p class="clinic-name">Pusat Perubatan Talvore</p><p>Level 12, Tower Annex 3, No. 8, Jalan Seri Bayu, 50470 Kuala Lumpur</p><p>Tel. No: +603-5550-1201 Fax No: +603-5550-1202</p><p>Email: kliniktalvore@example.com</p></div><span class="clinic-mark"></span></li>
      <li class="clinic"><div class="clinic-card"><p class="clinic-name">Klinik Talvore (Bukit Jelutong)</p><p>No. 22, Jalan Cempaka 4/2, 40160 Shah Alam, Selangor Darul Ehsan</p><p>Tel. No: +603-5550-2301 Fax No: +603-5550-2302</p><p>Email: kliniktalvore@example.com</p></div><span class="clinic-mark"></span></li>
      <li class="clinic"><div class="clinic-card"><p class="clinic-name">Klinik Talvore (Bayan Lepas)</p><p>Lot 5B-2-1, Persiaran Delima, Taman Rimba, 11950 Bayan Lepas, Penang</p><p>Tel. No: +604-555-3401 Fax No: +604-555-3402</p><p>Email: talvorepenang@example.com</p></div><span class="clinic-mark"></span></li>
      <li class="clinic"><div class="clinic-card"><p class="clinic-name">Klinik Talvore (Sendayan)</p><p>No. 41, Jalan Niaga Sendayan 2/5, 71960 Bandar Sri Sendayan</p><p>Tel. No: +606-555-4501 Fax No: +606-555-4502</p><p>Email: talvoresendayan@example.com</p></div><span class="clinic-mark"></span></li>
      <li class="clinic"><div class="clinic-card"><p class="clinic-name">Talvore Medical Clinic (KLIA)</p><p>Lot A-14, Arrival Level, Main Terminal Building, KLIA, 64000 Sepang</p><p>Tel. No: +603-5550-5601 Fax No: +603-5550-5602</p><p>Email: tmcklia1@example.com</p></div><span class="clinic-mark"></span></li>
      <li class="clinic"><div class="clinic-card"><p class="clinic-name">Talvore Medical Clinic (KLIA2)</p><p>L2-3-B07, Landside Arrival Level, KLIA2, 64000 Sepang, Selangor</p><p>Tel. No: +603-5550-6701 Fax No: +603-5550-6702</p><p>Email: tmcklia2@example.com</p></div><span class="clinic-mark"></span></li>
      <li class="clinic"><div class="clinic-card"><p class="clinic-name">Talvore Medical Clinic (PIA)</p><p>Unit L1-09, Passenger Terminal Building, Penang International Airport</p><p>Tel. No: +604-555-7801 Fax No: +604-555-7802</p><p>Email: talvoreclinic@example.com</p></div><span class="clinic-mark"></span></li>
    </ul>
  </section>

  <section class="page front">
    <svg width="560" height="791" viewBox="0 0 560 791">
      <defs>
        <linearGradient id="anatomyTone" x1="0" y1="0" x2="1" y2="1">
          <stop offset="0" stop-color="#cfd1d4"/><stop offset=".5" stop-color="#eef0f1"/><stop offset="1" stop-color="#b9bcc0"/>
        </linearGradient>
        <radialGradient id="organTone" cx=".5" cy=".5" r=".6">
          <stop offset="0" stop-color="#5fa8ee"/><stop offset="1" stop-color="#0b1f5a"/>
        </radialGradient>
      </defs>
      <rect class="anatomy" width="560" height="791" fill="url(#anatomyTone)" role="img" aria-label="Grey anatomical illustration of the human torso and organs"/>
      <polygon class="wedge-top" points="0,0 330,0 240,170 0,170" fill="var(--sky)"/>
      <polygon class="stripe" points="345,0 372,0 232,260 205,260" fill="var(--white)"/>
      <polygon class="panel" points="372,0 560,0 560,600 232,260" fill="var(--sky)"/>
      <polygon class="corner" points="560,600 560,791 420,791" fill="#a7aaae"/>
      <rect class="foot-band" y="771" width="560" height="20" fill="var(--blue)"/>
      <g class="organ-tiles" stroke="var(--white)" stroke-width="6" fill="url(#organTone)">
        <polygon points="110,170 170,170 200,225 170,280 110,280 80,225" role="img" aria-label="Illustration of the human brain"/>
        <polygon points="200,278 260,278 290,333 260,388 200,388 170,333" role="img" aria-label="Illustration of the ribcage and kidneys"/>
        <polygon points="310,386 370,386 400,441 370,496 310,496 280,441" role="img" aria-label="Illustration of the human heart"/>
        <polygon points="420,494 480,494 510,549 480,604 420,604 390,549" role="img" aria-label="Illustration of the internal organs"/>
      </g>
    </svg>
    <div class="brand"><div class="brand-dot"></div>TALVORE GROUP</div>
    <h2 class="report-title">MEDICAL REPORT</h2>
    <p class="tagline">"Your Healthcare Partner"</p>
    <p class="confidential">PRIVATE &amp;<br>CONFIDENTIAL</p>
  </section>

</main>
</body>
</html>
```